Counseling Practice Business Card

I need a professional looking business card incorporating my new logo that was just completed. Card needs to incorporate my name and title, description of my specialty, my address, my phone number, my fax number, my email and my website URL. I need to be able to choose design on/with different paper colors and textures.
I do not have a lot of business card ideas so I am open to anything but I want bold,sharp, clear card without additional designs other than my logo (see attached file info). I am open to different color backgrounds or paper colors including black. I do not like traditional brackets around area codes in phone number or dashes between numbers in phone number. Am open to other ways of presenting including periods between numbers as appropriate. I do not know enough to know what I like yet but I want card to coordinate and work together with my logo. My practice emphasizes natural mental health interventions so any use of color (with background paper color or the blue and green in my logo) that elicits nature is nice. In addition to black, any natural brown or wood looking background might be desirable also. Most of the offerings so far look very similar and boring.

Target Market(s)

Potential therapy clients and other professionals

Contact Information for Business Card

Card information:
Gerald M. Whitcombe, Ph.D.
Licensed Clinical Psychologist
Integrative Health Coach
4812 Marlowe Ridge Blvd SE
Suite 310
Alder Springs, GA 30412
(770) 415-2983 phone
(770) 581-4096 fax
drgeraldwhitcombe@quillmarsh.net
brightfernwellness.net

Font styles to use
Serif
Sans Serif
Other font styles liked:
• anything that you think looks crisp, clear and easily readable

Requirements
Must have
• Any color used should coordinate with my logo design (see attached files).
• Card should be printed horizontally so top and bottom are longest sides of rectangle.
• Background color or paper color should complement and highlight logo. Do not like a white background. black, grey, brown or any color my logo would blend well with.
Nice to have
• I would like designer to utilize color to highlight letters/name or phone-fax-web symbols.
• Bottom edge of card could be highlighted if appropriate to an idea.
Should not have
• I would NOT want the card to have a pure white background at all.
• No clear cards.
• Cards should be oriented with long sides on bottom and top, NOT sides. DO NOT LIKE THIS THIN TALL ORIENTATION.

```html
<!DOCTYPE html>
<html lang="en">
<head>
<meta charset="utf-8">
<title>Brightfern Wellness – Business Card</title>
<link rel="stylesheet" href="https://fonts.googleapis.com/css2?family=Roboto:wght@400;500&family=Roboto+Condensed:wght@500;700&display=swap">
<style>
  :root {
    --backdrop: #5b4230;
    --card-dark: #121314;
    --brand-blue: #2a72b6;
    --brand-green: #1c7a3c;
    --text-light: #d4d4d4;
    --divider: #3c3d40;
    --white: #ffffff;
  }
  * { margin: 0; padding: 0; box-sizing: border-box; }
  html, body {
    width: 1200px; height: 960px; overflow: hidden;
    background: var(--backdrop);
  }
  .canvas { position: relative; width: 1200px; height: 960px; }

  .card { position: absolute; width: 600px; height: 342px; box-shadow: 0 3px 8px rgba(0,0,0,.35); }

  /* Front */
  .card-front { left: 314px; top: 113px; background: var(--card-dark); overflow: hidden; }
  .front-brand {
    position: absolute; left: 36px; top: 142px; width: 220px;
    font-family: "Roboto", sans-serif; font-weight: 500;
    color: var(--brand-blue); text-align: center;
    font-size: 27px; line-height: 30px;
  }
  .divider { position: absolute; left: 282px; top: 66px; width: 1px; height: 208px; background: var(--divider); }
  .details { position: absolute; left: 311px; top: 66px; font-family: "Roboto", sans-serif; }
  .person-name {
    font-family: "Roboto Condensed", sans-serif; font-weight: 700;
    font-size: 20px; color: var(--brand-blue); letter-spacing: .2px; line-height: 24px;
  }
  .person-title {
    font-family: "Roboto Condensed", sans-serif; font-weight: 500;
    font-size: 16px; color: var(--brand-green); line-height: 19px;
  }
  .address { margin-top: 9px; font-size: 14px; line-height: 18px; color: var(--text-light); }
  .contacts { margin-top: 8px; list-style: none; font-size: 14px; line-height: 19px; color: var(--text-light); }
  .contacts li { display: flex; align-items: center; gap: 9px; }
  .contacts svg { width: 13px; height: 13px; fill: var(--brand-blue); flex: none; }
  .edge-band { position: absolute; left: 0; bottom: 0; width: 600px; height: 12px; }

  /* Back */
  .card-back { left: 312px; top: 472px; width: 599px; height: 343px; background: var(--brand-blue); }
  .back-brand {
    position: absolute; left: 0; right: 0; top: 118px;
    font-family: "Roboto", sans-serif; font-weight: 500;
    color: var(--white); text-align: center; font-size: 46px; line-height: 52px;
  }
  .back-url {
    position: absolute; left: 0; right: 0; top: 284px; text-align: center;
    font-family: "Roboto", sans-serif; font-size: 14px; letter-spacing: 3.3px; color: var(--white);
  }
</style>
</head>
<body>
<main class="canvas">

  <section class="card card-front" aria-label="Business card front">
    <div class="front-brand">Brightfern<br>Wellness</div>
    <div class="divider"></div>
    <div class="details">
      <h1 class="person-name">GERALD M. WHITCOMBE, PH.D.</h1>
      <p class="person-title">Licensed Clinical Psychologist</p>
      <p class="person-title">Integrative Health Coach</p>
      <p class="address">4812 Marlowe Ridge Blvd SE<br>Suite 310<br>Alder Springs, GA 30412</p>
      <ul class="contacts">
        <li><svg viewBox="0 0 16 16" aria-hidden="true"><path d="M3.6 1l2.6 3-1.4 1.8c.9 2 2.4 3.5 4.4 4.4L11 8.8l3 2.6-1.2 2.8C7 14 2 9 1.8 3.2z"/></svg>(770) 415-2983</li>
        <li><svg viewBox="0 0 16 16" aria-hidden="true"><path d="M4 1h8v4H4zM1 6h14v7h-3v2H4v-2H1zm4 5v3h6v-3z"/></svg>(770) 581-4096</li>
        <li><svg viewBox="0 0 16 16" aria-hidden="true"><path d="M1 3h14v1.5L8 9 1 4.5zM1 6.3l7 4.4 7-4.4V13H1z"/></svg>drgeraldwhitcombe@quillmarsh.net</li>
        <li><svg viewBox="0 0 16 16" aria-hidden="true"><circle cx="8" cy="8" r="7"/><path d="M1 8h14M8 1c-3 3.5-3 10.5 0 14M8 1c3 3.5 3 10.5 0 14" stroke="#121314" stroke-width="1" fill="none"/></svg>www.brightfernwellness.net</li>
      </ul>
    </div>
    <svg class="edge-band" viewBox="0 0 600 12" preserveAspectRatio="none" aria-hidden="true">
      <polygon points="0,0 396,0 392,12 0,12" fill="#2a72b6"/>
      <polygon points="398,0 600,0 600,12 394,12" fill="#1c7a3c"/>
    </svg>
  </section>

  <section class="card card-back" aria-label="Business card back">
    <div class="back-brand">Brightfern<br>Wellness</div>
    <p class="back-url">www.brightfernwellness.net</p>
  </section>

</main>
</body>
</html>
```